Lumen Fitness Personal Training Business

I need a business card design with a logo for my personal training company. I'd like the colors to be a vibrant green and black. I'd like the logo to incorporate an anvil (or something similar). I train hardcore competitive athletes as well as soccer moms trying to get and/or stay in shape. I need a logo that will not pigeon hole me in one category or the other, but at the same time not be too intimidating to soccer moms, but will not be off putting to the more hardcore trainees. The design should be attention grabbing and aesthetic.
Target Market(s)
Hardcore athletes as well as average people just trying to get/stay in shape.
Industry/Entity Type
Training

```html
<!DOCTYPE html>
<html lang="en">
<head>
<meta charset="utf-8">
<title>Lumen Fitness — Business Card</title>
<link rel="stylesheet" href="https://fonts.googleapis.com/css2?family=Open+Sans:wght@400;600;700&display=swap">
<style>
  :root {
    --green: #07a84e;
    --green-soft: #3fc36f;
    --black: #000000;
    --white: #ffffff;
    --backdrop: #d9d9d9;
    --rule: #2a2a2a;
  }
  * { box-sizing: border-box; margin: 0; padding: 0; }
  html, body {
    width: 1200px; height: 900px; overflow: hidden;
    background: var(--backdrop);
    font-family: "Open Sans", Arial, sans-serif;
  }
  .canvas {
    position: relative; width: 1200px; height: 900px;
  }
  .card {
    position: absolute; left: 250px;
    width: 700px; height: 400px;
    overflow: hidden;
    box-shadow: 0 6px 18px rgba(0,0,0,0.18);
  }
  .card--front { top: 30px; background: var(--black); }
  .card--back  { top: 470px; background: var(--green); }

  .band { position: absolute; left: 0; width: 100%; }
  .card--front .band--top    { top: 0; height: 75px; background: var(--green); }
  .card--front .band--bottom { top: 350px; height: 50px; background: var(--green); }
  .card--back .band--top     { top: 0; height: 170px; background: var(--black); }
  .card--back .band--bottom  { top: 372px; height: 28px; background: var(--black); }

  .brand {
    position: absolute; left: 0; width: 100%;
    display: flex; align-items: center; justify-content: center; gap: 22px;
  }
  .card--front .brand { top: 75px; height: 275px; }
  .card--back .brand  { top: 0; height: 170px; }
  .brand__dot {
    width: 46px; height: 46px; border-radius: 50%;
    background: var(--green-soft);
  }
  .card--back .brand__dot { background: var(--green); }
  .brand__rule { width: 1px; height: 82px; background: var(--rule); }
  .brand__name {
    color: var(--green-soft);
    font-weight: 600; font-size: 36px; line-height: 1.05;
    letter-spacing: 4px; text-transform: uppercase;
  }
  .card--back .brand__name { color: var(--green); }

  .person { position: absolute; left: 34px; top: 180px; color: var(--white); }
  .person__name { font-size: 26px; font-weight: 700; line-height: 1.1; }
  .person__role { font-size: 15px; font-weight: 400; margin-top: 2px; }

  .contact {
    position: absolute; right: 30px; top: 240px;
    list-style: none; color: var(--white);
    font-size: 19px; line-height: 24.5px; text-align: right;
  }
  .contact li { display: flex; align-items: center; justify-content: flex-end; gap: 10px; }
  .contact svg { width: 14px; height: 14px; fill: var(--white); flex: none; }
</style>
</head>
<body>
<main class="canvas">

  <section class="card card--front" aria-label="Business card front">
    <div class="band band--top"></div>
    <div class="brand">
      <span class="brand__dot"></span>
      <span class="brand__rule"></span>
      <span class="brand__name">Lumen<br>Fitness</span>
    </div>
    <div class="band band--bottom"></div>
  </section>

  <section class="card card--back" aria-label="Business card back">
    <div class="band band--top"></div>
    <div class="brand">
      <span class="brand__dot"></span>
      <span class="brand__rule"></span>
      <span class="brand__name">Lumen<br>Fitness</span>
    </div>

    <div class="person">
      <p class="person__name">Daniel Brooks</p>
      <p class="person__role">Managing Director</p>
    </div>

    <ul class="contact">
      <li>123.456.7890
        <svg viewBox="0 0 16 16" aria-hidden="true"><path d="M1 6c0-2 3-3 7-3s7 1 7 3v1h-3V5.5C11 5 9.5 5 8 5s-3 0-4 .5V7H1zM4 8h8l2 6H2z"/></svg></li>
      <li>123.456.7890
        <svg viewBox="0 0 16 16" aria-hidden="true"><path d="M4 1h8v4H4zM1 6h14v6h-3v3H4v-3H1zm4 4v3h6v-3z"/></svg></li>
      <li>info@youremail.com
        <svg viewBox="0 0 16 16" aria-hidden="true"><path d="M1 3h14v1L8 9 1 4zm0 3 7 5 7-5v7H1z"/></svg></li>
      <li>www.website.com
        <svg viewBox="0 0 16 16" aria-hidden="true"><path d="M6.5 9.5 9.5 6.5M7 4l1.5-1.5a3 3 0 0 1 4 4L11 8M9 12l-1.5 1.5a3 3 0 0 1-4-4L5 8" stroke="#fff" stroke-width="1.8" fill="none" stroke-linecap="round"/></svg></li>
      <li>1234, Address Goes Here, Country Name, 123456
        <svg viewBox="0 0 16 16" aria-hidden="true"><path d="M8 0a5.5 5.5 0 0 1 5.5 5.5C13.5 10 8 16 8 16S2.5 10 2.5 5.5A5.5 5.5 0 0 1 8 0zm0 3.5a2 2 0 1 0 0 4 2 2 0 0 0 0-4z"/></svg></li>
    </ul>

    <div class="band band--bottom"></div>
  </section>

</main>
</body>
</html>
```